Thornvale Agribusiness Consulting needs a Website Design.

We need a website design for a new company based in UK. Thornvale offers agribusiness consulting and farm design services to farmers, smallholders and the wider agribusiness industry to assist clients in adopting more sustainable and regenerative production, processing and marketing practices.
Services are offered face-to-face and on a remote platform.
Services are offered in the UK and overseas.
We would like to see designs that reflect the natural environment, business and sustainability. Desired colours; green, blue, grey. The final design should communicate professionalism in the rural economy.
The design should be able to be customized by the client to make future changes and additions.
Target Market(s)
Farmers, smallholders, and the agricultural industry in UK and overseas.
Industry/Entity Type
Agribusiness
Number of Pages Required
4 page
Look and feel
Each slider illustrates characteristics of the customer's brand and the style your logo design should communicate.

```html
<!DOCTYPE html>
<html lang="en">
<head>
<meta charset="utf-8">
<title>Thornvale – Agribusiness Consulting</title>
<link href="https://fonts.googleapis.com/css2?family=Varela+Round&family=Nunito:ital,wght@0,400;0,600;0,700;1,400&display=swap" rel="stylesheet">
<style>
:root{
  --green:#8cc42d;
  --green-dark:#6fa51c;
  --blue:#1a85cf;
  --blue-light:#2e9fe0;
  --blue-deep:#1572bd;
  --grey-bar:#e6e6e6;
  --text:#444;
  --muted:#666;
  --footer:#3a3a3a;
  --white:#fff;
}
*{margin:0;padding:0;box-sizing:border-box}
html,body{width:705px;height:1200px;overflow:hidden;background:#fff}
body{font-family:"Nunito",sans-serif;color:var(--text);position:relative}
.abs{position:absolute}
h1,h2,h3{font-family:"Varela Round",sans-serif;font-weight:400}

.topbar{left:38px;top:0;width:628px;height:24px;background:var(--grey-bar);clip-path:polygon(0 0,100% 0,98.8% 100%,1.2% 100%);font-size:7.5px;color:#333;display:flex;align-items:center;justify-content:space-between;padding:0 18px}
.social{display:flex;align-items:center;gap:4px}
.social span.dot{width:13px;height:13px;border-radius:50%;display:inline-block}
.contact b{font-weight:600}
.contact .val{color:var(--blue)}
.contact .val.mail{color:var(--green-dark)}

.logo{left:44px;top:33px;font-family:"Varela Round",sans-serif;font-size:21px;color:var(--blue)}
.search{left:532px;top:34px;width:129px;height:23px;border:1px solid #bbb;font-size:7px;color:#888;display:flex;align-items:center;justify-content:space-between;padding:0 6px}

.nav{left:38px;top:66px;width:628px;height:21px;background:var(--green);display:flex;align-items:center;justify-content:space-around;padding:0 20px;font-size:8px;color:#fff;letter-spacing:.2px}
.navline{left:0;top:86px;width:705px;height:4px;background:var(--green)}

.hero-photo{left:0;top:90px;width:705px;height:247px;background:linear-gradient(180deg,#8f989f 0%,#b9c0c4 45%,#a3aca8 62%,#6b8f3c 80%,#5a8a2c 100%)}
.hero-title{left:44px;top:134px;width:340px;font-size:16px;line-height:21px;color:var(--blue)}
.hero-text{left:44px;top:179px;width:300px;font-size:11px;line-height:14.5px;color:#111}
.btn{left:44px;top:230px;width:76px;height:22px;background:var(--green);border:1px solid #6a9c1e;color:#fff;font-size:7.5px;display:flex;align-items:center;justify-content:center}
.dots{left:44px;top:264px;display:flex;gap:3px}
.dots i{width:6px;height:6px;border-radius:50%;background:#fff;display:block}
.dots i.on{background:var(--blue-light)}

.section-title{left:0;width:705px;text-align:center;font-size:14px;color:var(--green)}
.welcome-text{left:55px;top:382px;width:595px;text-align:center;font-size:7.5px;line-height:13px;color:var(--muted)}

.services{left:0;top:442px;width:705px;height:250px;background:var(--green)}
.services .section-title{top:20px;color:#fff}
.card{top:52px;width:142px;height:175px;background:linear-gradient(180deg,var(--blue-light),var(--blue-deep));text-align:center;color:#fff;box-shadow:0 6px 6px -4px rgba(0,0,0,.3)}
.card::before{content:"";position:absolute;left:60px;top:0;border-left:11px solid transparent;border-right:11px solid transparent;border-top:11px solid var(--green)}
.card svg{position:absolute;left:38px;top:22px}
.card h3{position:absolute;top:100px;width:100%;font-size:9.5px;line-height:13px}
.card p{position:absolute;top:130px;left:10px;right:10px;font-size:7px;line-height:10.5px;color:#e3f0fb}

.gallery-title{top:715px;left:0;width:705px;display:flex;justify-content:center;align-items:center;gap:10px;font-family:"Varela Round",sans-serif;color:var(--green);font-size:14px}
.circle-arrow{width:19px;height:19px;border-radius:50%;border:1px solid #777;display:flex;align-items:center;justify-content:center;background:#fff}
.photo{top:744px;width:142px;height:99px}

.blog{left:0;top:866px;width:705px;height:142px;background:linear-gradient(180deg,#3b9ed9,#1a7ac7)}
.blog h2{position:absolute;left:43px;top:23px;font-size:14px;color:#fff}
.blog .arrows{position:absolute;left:617px;top:19px;display:flex;gap:7px}
.blog .arrows .circle-arrow{border-color:#fff}
.post-img{top:56px;width:105px;height:65px;border:2px solid #5fb5e8}
.post-text{top:55px;width:185px;font-size:7.5px;line-height:12.5px;color:#d6ecfa}
.post-text em{display:block;margin-top:4px;color:#b9e36a;font-size:7px}

.quote{left:72px;top:1052px;width:562px;text-align:center;font-size:7.5px;line-height:13px;font-style:italic;color:var(--muted)}
.qmark{top:1048px;font-family:Georgia,serif;font-size:22px;color:var(--green);font-weight:700}
.name{top:1097px;left:0;width:705px;text-align:center;font-size:8px;color:var(--blue)}
.loc{top:1109px;left:0;width:705px;text-align:center;font-size:7px;font-style:italic;color:#888}

.footer{left:0;top:1138px;width:705px;height:62px;background:var(--footer)}
.footer nav{position:absolute;top:17px;width:100%;display:flex;justify-content:center;gap:20px;font-size:7.5px;color:#eee}
.footer p{position:absolute;top:37px;width:100%;text-align:center;font-size:6.5px;color:#ddd}
.footer p span{color:var(--blue)}
</style>
</head>
<body>

<header>
  <div class="abs topbar">
    <div class="social">Connect us:
      <span class="dot" style="background:#2d4c8c"></span>
      <span class="dot" style="background:#1da1f2"></span>
      <span class="dot" style="background:#0a66a8"></span>
      <span class="dot" style="background:#f2711c"></span>
    </div>
    <div class="contact"><b>CALL US:</b> <span class="val">020-555-0142</span> &nbsp;|&nbsp; <b>EMAIL US:</b> <span class="val mail">hello@thornvale-consult.co.uk</span></div>
  </div>
  <div class="abs logo">Thornvale</div>
  <div class="abs search">Search...
    <svg width="11" height="11" viewBox="0 0 12 12"><circle cx="5" cy="5" r="3.5" fill="none" stroke="#1a85cf" stroke-width="1.6"/><line x1="7.5" y1="7.5" x2="11" y2="11" stroke="#1a85cf" stroke-width="2"/></svg>
  </div>
  <nav class="abs nav"><span>HOME</span><span>ABOUT US</span><span>SERVICES</span><span>OUR CLIENTS</span><span>BLOGS</span><span>CAREERS</span><span>LATEST NEWS</span><span>CONTACT US</span></nav>
  <div class="abs navline"></div>
</header>

<section class="hero-slider">
  <div class="abs hero-photo" role="img" aria-label="Photo of a lone oak tree in a green field under a cloudy sky"></div>
  <h1 class="abs hero-title">Thornvale Offers Agribusiness Consulting and Farm Design Services to Farmers</h1>
  <p class="abs hero-text">Duis aliquam nibh a dui iaculis viverra id a velit. Vivamus egestas risus in magna varius commodo. Sed semper viverra egestas.</p>
  <div class="abs btn">READ MORE</div>
  <div class="abs dots"><i class="on"></i><i></i><i></i><i></i></div>
</section>

<section class="welcome">
  <h2 class="abs section-title" style="top:358px">WELCOME TO OUR WEBSITE</h2>
  <p class="abs welcome-text">Aliquam molestie, mi et imperdiet euismod, dui purus auctor tellus, et interdum lacus lectus et ante. Sed accumsan sollicitudin sapien, sit amet adipiscing turpis gravida ac. In congue, neque ac lobortis volutpat, libero mauris varius mi, vitae suscipit ipsum ligula vitae risus. Duis aliquam nibh a dui iaculis viverra id a velit. Vivamus egestas risus in magna varius commodo. Sed semper viverra egestas. Etiam pretium porttitor lectus, vel ornare neque porta volutpat.</p>
</section>

<section class="abs services">
  <h2 class="abs section-title">WHAT WE DO</h2>
  <div class="abs card" style="left:44px">
    <svg width="66" height="66" viewBox="0 0 66 66"><circle cx="33" cy="33" r="31" fill="none" stroke="#fff" stroke-width="2"/><path d="M17 28h6v12h-6zM43 28h6v12h-6zM23 30l7-3 6 2 7-1v10l-6 4-7-5-7 3z" fill="#fff"/></svg>
    <h3>AGRI BUSINESS<br>CONSULTING</h3>
    <p>Sed accumsan sollicitudin sapien, sit amet adipiscing turpis gravida ac.</p>
  </div>
  <div class="abs card" style="left:202px">
    <svg width="66" height="66" viewBox="0 0 66 66"><circle cx="33" cy="33" r="31" fill="none" stroke="#fff" stroke-width="2"/><circle cx="33" cy="26" r="9" fill="#fff"/><rect x="31.5" y="30" width="3" height="14" fill="#fff"/><path d="M18 46q15-6 30 0" fill="none" stroke="#fff" stroke-width="2"/></svg>
    <h3>FARM DESIGN FOR<br>FARMERS</h3>
    <p>Sed accumsan sollicitudin sapien, sit amet adipiscing turpis gravida ac.</p>
  </div>
  <div class="abs card" style="left:362px">
    <svg width="66" height="66" viewBox="0 0 66 66"><circle cx="33" cy="33" r="31" fill="none" stroke="#fff" stroke-width="2"/><path d="M33 32q-10-2-10-12q10 0 10 12zM33 32q10-2 10-12q-10 0-10 12z" fill="#fff"/><path d="M18 32q3 10 15 14q12-4 15-14l-4 1q-3 7-11 9q-8-2-11-9z" fill="#fff"/></svg>
    <h3>SUSTAINABLE<br>PRODUCTION</h3>
    <p>Sed accumsan sollicitudin sapien, sit amet adipiscing turpis gravida ac.</p>
  </div>
  <div class="abs card" style="left:519px">
    <svg width="66" height="66" viewBox="0 0 66 66"><circle cx="33" cy="33" r="31" fill="none" stroke="#fff" stroke-width="2"/><path d="M18 29h6l14-8v24l-14-8h-6z" fill="#fff"/><path d="M24 37l3 9h4l-2-9z" fill="#fff"/><path d="M42 27l6-3M43 33h6M42 39l6 3" stroke="#fff" stroke-width="2"/></svg>
    <h3>MARKETING<br>PRACTICES</h3>
    <p>Sed accumsan sollicitudin sapien, sit amet adipiscing turpis gravida ac.</p>
  </div>
</section>

<section class="gallery">
  <div class="abs gallery-title">
    <span class="circle-arrow"><svg width="6" height="8" viewBox="0 0 6 8"><path d="M5 0L1 4l4 4" fill="none" stroke="#333"/></svg></span>
    PHOTO GALLERY
    <span class="circle-arrow"><svg width="6" height="8" viewBox="0 0 6 8"><path d="M1 0l4 4-4 4" fill="none" stroke="#333"/></svg></span>
  </div>
  <div class="abs photo" style="left:44px;background:linear-gradient(180deg,#6f9a4a,#5f9a32)" role="img" aria-label="Photo of cattle grazing in a green pasture"></div>
  <div class="abs photo" style="left:203px;background:linear-gradient(180deg,#4f8ed8,#7f9c6a)" role="img" aria-label="Photo of a field of green crop beside ploughed soil under blue sky"></div>
  <div class="abs photo" style="left:361px;background:linear-gradient(180deg,#c9a060,#b98a44)" role="img" aria-label="Photo of round hay bales in a harvested field"></div>
  <div class="abs photo" style="left:520px;background:linear-gradient(180deg,#7f8a86,#66713f)" role="img" aria-label="Photo of a wooden farm gate by a meadow"></div>
</section>

<section class="abs blog">
  <h2>BLOG POST</h2>
  <div class="arrows">
    <span class="circle-arrow"><svg width="6" height="8" viewBox="0 0 6 8"><path d="M5 0L1 4l4 4" fill="none" stroke="#333"/></svg></span>
    <span class="circle-arrow"><svg width="6" height="8" viewBox="0 0 6 8"><path d="M1 0l4 4-4 4" fill="none" stroke="#333"/></svg></span>
  </div>
  <div class="abs post-img" style="left:44px;background:linear-gradient(180deg,#8a6a3a,#6b7a3a)" role="img" aria-label="Photo of locally grown vegetables in crates"></div>
  <p class="abs post-text" style="left:162px">Aliquam molestie, mi et imperdiet euismod, dui purus auctor tellus, et interdum lacus lectus et ante. Sed accumsan sollicitudin sapien, sit amet adipiscing turpis gravida ac.<em>Posted on 3 days ago</em></p>
  <div class="abs post-img" style="left:362px;background:linear-gradient(180deg,#ece9e4,#d8d3cc)" role="img" aria-label="Photo of a tray of eggs"></div>
  <p class="abs post-text" style="left:479px">Aliquam molestie, mi et imperdiet euismod, dui purus auctor tellus, et interdum lacus lectus et ante. Sed accumsan sollicitudin sapien, sit amet adipiscing turpis gravida ac.<em>Posted on 3 days ago</em></p>
</section>

<section class="testimonial">
  <h2 class="abs section-title" style="top:1026px">WHAT OUR CLIENT SAYS...</h2>
  <span class="abs qmark" style="left:45px">&ldquo;</span>
  <p class="abs quote">Aliquam molestie, mi et imperdiet euismod, dui purus auctor tellus, et interdum lacus lectus et ante. Sed accumsan sollicitudin sapien, sit amet adipiscing turpis gravida ac. In congue, neque ac lobortis volutpat, libero mauris varius mi, vitae suscipit ipsum ligula vitae risus. Duis aliquam nibh a dui iaculis viverra id a velit. Vivamus egestas risus in magna varius commodo. Sed semper viverra egestas. Etiam pretium porttitor lectus, vel ornare neque porta volutpat.</p>
  <span class="abs qmark" style="left:645px">&rdquo;</span>
  <div class="abs name">Name Heading</div>
  <div class="abs loc">Location</div>
</section>

<footer class="abs footer">
  <nav><span>Home</span><span>About Us</span><span>Services</span><span>Our Clients</span><span>Blogs</span><span>Careers</span><span>Latest News</span><span>Contact Us</span></nav>
  <p>Copyright ©2015.<span>Thornvale</span>.All Right Reserved</p>
</footer>

</body>
</html>
```